Building Design company needing a letterhead

We need a letter head for our Building Design company to send letters etc. to our clients, consultants, councils etc. We would like to see our logo used and company colours. I have attached our style guide and an example of our current letterheads. Top left we would like our logo, top right we would like the company details and at the footer we would like some sort of image/design etc. that suits our brand. I like the Tarrow Design letterhead attached.

Target Market(s)

Professionals, Councils, Consultants, Mums & Dads

Industry/Entity Type

Architecture

Other font styles liked:
• refer the design style guide

Colors
f37122
000000
1b1b1b

Requirements
Must have
• Must have the minimum of a logo, company details and footer
Nice to have
• An image/design made for the footer that would suite our brand and website at www.corvanplans.com.au. Also it would be nice to include the KMEOT logo somewhere perhaps included in the footer.
Should not have
• Large images in the header. I just want the logo and company details.

```html
<!DOCTYPE html>
<html lang="en">
<head>
<meta charset="utf-8">
<title>Corvan Plans — Letterhead</title>
<link href="https://fonts.googleapis.com/css2?family=Arimo:wght@400&family=Open+Sans:wght@400;700&display=swap" rel="stylesheet">
<style>
  :root {
    --brand-orange: #f37122;
    --brand-black: #000000;
    --ink: #1b1b1b;
    --body-ink: #2a2a2a;
    --paper: #f8f8f8;
    --backdrop: #e4e2de;
  }
  * { margin: 0; padding: 0; box-sizing: border-box; }
  html, body {
    width: 1189px;
    height: 1200px;
    overflow: hidden;
    background: var(--backdrop);
  }
  .letterhead {
    position: absolute;
    left: 132px;
    top: 0;
    width: 925px;
    height: 1200px;
    background: var(--paper);
  }
  .brand {
    position: absolute;
    left: 75px;
    top: 62px;
    display: flex;
    align-items: center;
    gap: 22px;
  }
  .brand-square {
    width: 96px;
    height: 96px;
    background: var(--brand-orange);
  }
  .brand-name {
    font-family: "Open Sans", sans-serif;
    font-weight: 700;
    font-size: 46px;
    line-height: 48px;
    letter-spacing: 2px;
    color: var(--ink);
    text-transform: uppercase;
  }
  .contact {
    position: absolute;
    left: 530px;
    top: 64px;
    list-style: none;
    font-family: "Open Sans", sans-serif;
    font-size: 15px;
    line-height: 20.2px;
    color: var(--ink);
  }
  .contact li { display: flex; align-items: center; gap: 6px; white-space: nowrap; }
  .contact svg { width: 13px; height: 13px; flex: none; }
  .contact .abn-label { color: var(--brand-orange); margin-left: 14px; }
  .letter-body {
    position: absolute;
    left: 75px;
    top: 288px;
    width: 777px;
    font-family: "Arimo", sans-serif;
    font-size: 17.4px;
    line-height: 27.4px;
    color: var(--body-ink);
    hyphens: auto;
  }
  .letter-body p + p { margin-top: 27.4px; }
  .letter-body p.section-break { margin-top: 54px; }
  .affiliation {
    position: absolute;
    left: 800px;
    top: 1058px;
    width: 76px;
    display: flex;
    flex-direction: column;
    align-items: center;
    gap: 4px;
  }
  .affiliation-square {
    width: 70px;
    height: 70px;
    border: 3px solid var(--brand-orange);
  }
  .affiliation-name {
    font-family: "Open Sans", sans-serif;
    font-weight: 400;
    font-size: 17px;
    letter-spacing: 1px;
    color: var(--brand-orange);
  }
</style>
</head>
<body>
<main class="letterhead">
  <header>
    <div class="brand">
      <div class="brand-square"></div>
      <div class="brand-name">Corvan<br>Plans</div>
    </div>
    <ul class="contact">
      <li>
        <svg viewBox="0 0 13 13"><rect width="13" height="13" fill="var(--brand-orange)"/><path d="M2.5 3.5h8v6h-8z M2.5 3.5l4 3.2 4-3.2" fill="none" stroke="#fff" stroke-width="1.1"/></svg>
        admin@corvanplans.com.au
      </li>
      <li>
        <svg viewBox="0 0 13 13"><rect width="13" height="13" fill="var(--brand-orange)"/><circle cx="6.5" cy="6.5" r="4" fill="none" stroke="#fff" stroke-width="1"/><path d="M2.5 6.5h8 M6.5 2.5v8" stroke="#fff" stroke-width="0.9"/></svg>
        www.corvanplans.com.au
      </li>
      <li>
        <svg viewBox="0 0 13 13"><rect width="13" height="13" fill="var(--brand-orange)"/><path d="M6.5 11 C4 8 3.5 6.8 3.5 5.5 a3 3 0 0 1 6 0 c0 1.3-.5 2.5-3 5.5z" fill="#fff"/><circle cx="6.5" cy="5.5" r="1.1" fill="var(--brand-orange)"/></svg>
        Unit 3/22 Harlow Street Westbrook WA 6180
      </li>
      <li>
        <svg viewBox="0 0 13 13"><rect width="13" height="13" fill="var(--brand-orange)"/><path d="M6.5 11 C4 8 3.5 6.8 3.5 5.5 a3 3 0 0 1 6 0 c0 1.3-.5 2.5-3 5.5z" fill="#fff"/><circle cx="6.5" cy="5.5" r="1.1" fill="var(--brand-orange)"/></svg>
        PO Box 5187 Westbrook North WA 6180
      </li>
      <li>
        <svg viewBox="0 0 13 13"><rect width="13" height="13" fill="var(--brand-orange)"/><path d="M3 5 q3.5-3 7 0 l-1.3 1.2-1.2-.8v-.9h-2v.9l-1.2.8z M4.2 7.2h4.6l.6 3h-5.8z" fill="#fff"/></svg>
        (08) 6142 7390 <span class="abn-label">ABN</span>&nbsp;61 408 213 770
      </li>
    </ul>
  </header>

  <section class="letter-body">
    <p>Lorem Ipsum is simply dummy text of the printing and typesetting industry. Lorem Ipsum has been the industry’s standard dummy text ever since the 1500s, when an unknown printer took a galley of type and scrambled it to make a type specimen book. It has survived not only five centuries, but also the leap into electronic typesetting, remaining essentially unchanged. It was popularised in the 1960s with the release of Typeline sheets containing Lorem Ipsum passages, and more recently with desktop publishing software like Quillset Layout including versions of Lorem Ipsum.</p>
    <p>It is a long established fact that a reader will be distracted by the readable content of a page when looking at its layout. The point of using Lorem Ipsum is that it has a more-or-less normal distribution of letters, as opposed to using ’Content here, content here’, making it look like readable English. Many desktop publishing packages and web page editors now use Lorem Ipsum as their default model text, and a search for ’lorem ipsum’ will uncover many web sites still in their infancy. Various versions have evolved over the years, sometimes by accident, sometimes on purpose (injected humour and the like).</p>
    <p class="section-break">Contrary to popular belief, Lorem Ipsum is not simply random text. It has roots in a piece of classical Latin literature from 45 BC, making it over 2000 years old. Henry Aldwell, a Latin professor at Marlowe College in Vermont, looked up one of the more obscure Latin words, consectetur, from a Lorem Ipsum passage, and going through the cites of the word in classical literature, discovered the undoubtable source. Lorem Ipsum comes from sections 1.10.32 and 1.10.33 of "de Finibus Bonorum et Malorum" structures, to generate Lorem Ipsum which looks reasonable. The generated Lorem Ipsum is therefore always free from repetition, injected humour, or non-characteristic words etc.</p>
  </section>

  <footer class="affiliation">
    <div class="affiliation-square"></div>
    <div class="affiliation-name">KMEOT</div>
  </footer>
</main>
</body>
</html>
```